Business Card Design For A Renovation Contractor Company

We need a business card for a new company based in Singapore, our company name is "RB Tolvane". We are a renovation contractor that builds designs into reality. We build more of F&B restaurants, retail stores and commercial offices. We work very closely with designers. The final design should communicate to our client that we are a company that you can trust, that will plan and complete your project without giving you a headache. I like my client to remember my company as "RB". The beauty of SIMPLE is important.

Industry/Entity Type

Contractor

Requirements
Nice to have
• Black or Red base

```html
<!DOCTYPE html>
<html lang="en">
<head>
<meta charset="utf-8">
<title>RB Tolvane — Business Card</title>
<link href="https://fonts.googleapis.com/css2?family=Questrial&family=Arimo:wght@700&display=swap" rel="stylesheet">
<style>
  :root {
    --brand-red: #e8202a;
    --ink: #231f20;
    --grey-text: #555555;
    --swoosh-grey: #6d6e71;
    --paper: #ffffff;
    --backdrop: #ecebe8;
  }
  * { margin: 0; padding: 0; box-sizing: border-box; }
  html, body { width: 1200px; height: 720px; overflow: hidden; }
  body {
    background: var(--backdrop);
    font-family: "Questrial", "Century Gothic", sans-serif;
    position: relative;
  }
  .card {
    position: absolute;
    top: 205px;
    width: 540px;
    height: 309px;
    border-radius: 4px;
    overflow: hidden;
    box-shadow: 0 6px 18px rgba(0,0,0,0.18);
  }
  .card--front { left: 40px; background: var(--paper); }
  .card--back { left: 620px; background: var(--brand-red); }

  .front-curve { position: absolute; inset: 0; width: 100%; height: 100%; }

  .brand-block {
    position: absolute;
    top: 34px;
    left: 0;
    width: 100%;
    text-align: center;
  }
  .brand-name {
    font-size: 46px;
    line-height: 1;
    color: var(--ink);
    letter-spacing: -0.5px;
  }
  .brand-tagline {
    display: inline-block;
    margin-top: 6px;
    padding: 2px 6px 3px;
    border-top: 2px solid var(--ink);
    font-size: 17px;
    color: var(--ink);
    letter-spacing: 0.3px;
  }
  .address {
    position: absolute;
    top: 148px;
    right: 22px;
    font-size: 13.5px;
    letter-spacing: 1px;
    color: var(--grey-text);
  }

  .person {
    position: absolute;
    left: 118px;
    top: 232px;
    text-align: right;
    color: var(--paper);
  }
  .person-name {
    font-family: "Arimo", Arial, sans-serif;
    font-weight: 700;
    font-size: 19px;
    line-height: 1.1;
  }
  .person-title { font-size: 13px; }
  .contact-divider {
    position: absolute;
    left: 254px;
    top: 214px;
    width: 1.5px;
    height: 66px;
    background: var(--paper);
  }
  .contact-list {
    position: absolute;
    left: 268px;
    top: 208px;
    list-style: none;
    color: var(--paper);
    font-size: 13px;
    line-height: 17.5px;
    letter-spacing: 0.4px;
  }

  .back-mark {
    position: absolute;
    top: 112px;
    left: 0;
    width: 100%;
    display: flex;
    justify-content: center;
    align-items: center;
    gap: 16px;
    color: var(--paper);
  }
  .back-dot {
    width: 40px;
    height: 40px;
    border-radius: 50%;
    background: var(--paper);
  }
  .back-name { font-size: 50px; line-height: 1; }
  .back-url {
    position: absolute;
    right: 40px;
    bottom: 34px;
    color: var(--paper);
    font-size: 18px;
    letter-spacing: 3px;
  }
</style>
</head>
<body>
  <section class="card card--front" aria-label="Business card front">
    <svg class="front-curve" viewBox="0 0 540 309" preserveAspectRatio="none" aria-hidden="true">
      <path d="M0,248 C160,200 340,178 540,168 L540,174 C340,186 160,208 0,256 Z" fill="var(--swoosh-grey)"/>
      <path d="M0,262 C160,214 340,190 540,180 L540,309 L0,309 Z" fill="var(--brand-red)"/>
    </svg>
    <div class="brand-block">
      <div class="brand-name">RB Tolvane</div>
      <div class="brand-tagline">building reality with a plan</div>
    </div>
    <p class="address">Door No. Street Name City Name, State, Zip Code.</p>
    <div class="person">
      <div class="person-name">Your Name</div>
      <div class="person-title">Title</div>
    </div>
    <div class="contact-divider"></div>
    <ul class="contact-list">
      <li>p: 123-456-7890</li>
      <li>c: 123-456-7890</li>
      <li>e: info@rbtolvane.com</li>
      <li>w: www.rbtolvane.com</li>
    </ul>
  </section>

  <section class="card card--back" aria-label="Business card back">
    <div class="back-mark">
      <span class="back-dot"></span>
      <span class="back-name">RB Tolvane</span>
    </div>
    <p class="back-url">www.rbtolvane.com</p>
  </section>
</body>
</html>
```